Animal Horse & Bedding Company Needs a Website Coded & Designed

We need a website for a new animal bedding and feed company that is visually grabbing and vibrant. We would like to see a website that displays trust, quality and confidence. Needs to be responsive and mobile friendly for all browsers and coded for both Android & IOS. SEO is also important.

Joomla or Wordpress – must be both desktop and mobile friendly with fast page load speed. Need the ability to edit ourselves in Wordpress or Joomla.

Full details attached below with some layout and content ideas.

Coding

Coded - Design and coding required

Number of Pages Required

5+ page

Font styles to use
Sans Serif

Requirements
Must have
• Needs to be responsive and mobile friendly for all browsers and coded for both Android & IOS. SEO is also important.

Wordpress – must be both desktop and mobile friendly with fast page load speed. Need the ability to edit ourselves in Wordpress.

Logo Colours:
Dark Brown
CMYK: 50 / 70 / 80 / 70
Pantone: 4625C

Orange
CMYK: 0 / 50 / 100 / 0
Pantone: 144C
Nice to have
• Use picture of building attached and super impose logo on building.

```html
<!DOCTYPE html>
<html lang="en">
<head>
<meta charset="utf-8">
<title>Golden Sheaf Bedding &amp; Feed</title>
<link href="https://fonts.googleapis.com/css2?family=Bebas+Neue&family=Roboto+Condensed:wght@400;700&family=Roboto:wght@400;500;700&display=swap" rel="stylesheet">
<style>
:root{
  --brown:#4a2511;
  --brown-deep:#3a1c0c;
  --ink:#3b1f0e;
  --orange:#f7931e;
  --orange-deep:#e07f0c;
  --grey:#e9e9e9;
  --text:#555;
  --white:#fff;
}
*{margin:0;padding:0;box-sizing:border-box}
html,body{width:1200px;height:4405px;overflow:hidden}
body{position:relative;background:var(--white);font-family:"Roboto",sans-serif;color:var(--text)}
.abs{position:absolute}
.display{font-family:"Bebas Neue",sans-serif;font-weight:400;letter-spacing:.5px}
.cond{font-family:"Roboto Condensed",sans-serif}

/* top bar */
.topbar{left:0;top:0;width:1200px;height:34px;background:var(--orange);display:flex;justify-content:flex-end;align-items:center;gap:10px;padding-right:117px;color:var(--white);font-family:"Bebas Neue",sans-serif;font-size:17px;letter-spacing:.8px}
.dots{display:flex;gap:3px}
.dots i{display:block;width:12px;height:12px;border-radius:50%;background:var(--ink)}

/* hero */
.hero{left:0;top:34px;width:1200px;height:666px;background:linear-gradient(180deg,#b9c4c9 0%,#8fa07a 14%,#6d7d4f 30%,#8a3a2c 42%,#6f7a52 55%,#5b4a2a 72%,#4a2511 86%,#4a2511 100%)}
.hero-curve{left:0;top:560px}
.header{left:0;top:34px;width:1200px;height:115px}
.brand{display:flex;align-items:center;gap:10px}
.brand-mark{width:40px;height:40px;border-radius:50%;background:var(--orange)}
.brand-name{font-family:"Bebas Neue",sans-serif;font-size:34px;letter-spacing:2px;color:var(--ink);line-height:1}
.header .brand{position:absolute;left:108px;top:32px}
.nav{position:absolute;left:432px;top:48px;display:flex;gap:0}
.nav a{font-family:"Bebas Neue",sans-serif;font-size:18px;color:var(--ink);text-decoration:none;letter-spacing:.6px}
.nav a:nth-child(1){margin-right:68px}
.nav a:nth-child(2){margin-right:72px}
.nav a:nth-child(3){margin-right:72px}
.nav a:nth-child(4){margin-right:72px}
.btn-quote{left:966px;top:79px;width:120px;height:30px;background:var(--brown);border:1px solid var(--orange);color:var(--orange);font-family:"Bebas Neue",sans-serif;font-size:17px;display:flex;align-items:center;justify-content:center;letter-spacing:.6px}
.hero-title{left:0;top:448px;width:1200px;text-align:center;color:var(--white);font-size:58px;line-height:56px}
.hero-btns{left:0;top:574px;width:1200px;display:flex;justify-content:center;gap:14px}
.btn{font-family:"Bebas Neue",sans-serif;font-size:17px;letter-spacing:.6px;height:28px;display:flex;align-items:center;justify-content:center}
.btn-solid{background:var(--orange);color:var(--ink);width:120px}
.btn-line{border:1.5px solid var(--orange);color:var(--orange);width:120px}
.arrow{top:484px;width:16px;height:16px;border-top:2.5px solid var(--white);border-left:2.5px solid var(--white)}

/* section headings */
.sec-title{display:flex;align-items:center;gap:10px;font-family:"Bebas Neue",sans-serif;font-size:52px;line-height:1;color:var(--ink)}
.sec-title .ring{width:30px;height:30px;border-radius:50%;border:5px solid var(--orange)}
.sec-title.light{color:var(--orange)}

/* about */
.about-title{left:114px;top:756px}
.about-sub{left:116px;top:830px;font-family:"Bebas Neue",sans-serif;font-size:20px;color:var(--ink);letter-spacing:.5px}
.about-text{left:116px;top:853px;width:420px;font-size:12px;line-height:15.5px;color:#666}
.about-text p{margin-bottom:15px}
.about-img{left:560px;top:740px;width:540px;height:300px;border-radius:6px;background:radial-gradient(ellipse at 40% 55%,#6b4a33 0%,#b08a68 35%,#f3ece4 70%,#fff 100%)}
.feature{top:1058px;display:flex;gap:10px;align-items:flex-start}
.feature .ico{width:44px;height:44px;border-radius:50%;background:var(--orange);border:3px solid #fbd3a0;flex:none;display:flex;align-items:center;justify-content:center}
.feature h4{font-family:"Bebas Neue",sans-serif;font-weight:400;font-size:18px;color:var(--ink);margin-top:2px;letter-spacing:.4px}
.feature p{font-size:9.5px;line-height:12px;color:#555;width:170px}
.divider{top:1052px;width:2px;height:54px;background:#c9b9a8}

/* services */
.services-bg{left:0;top:1148px;width:1200px;height:1467px;background:var(--brown)}
.curve{left:0}
.services-title{left:0;top:1328px;width:1200px;justify-content:center}
.svc{left:111px;top:1453px;width:954px;height:971px;border:1.5px solid var(--orange)}
.ph{position:absolute}
.svc-img1{left:111px;top:1453px;width:478px;height:486px;background:linear-gradient(160deg,#9a5a2a 0%,#d9a24a 40%,#e9bf5d 70%,#c98d34 100%)}
.svc-img2{left:589px;top:1938px;width:476px;height:486px;background:linear-gradient(135deg,#e8e0d4 0%,#b9aa97 35%,#d6a750 60%,#7a6a58 100%)}
.svc-text{color:var(--white);width:390px}
.svc-text h3{font-family:"Bebas Neue",sans-serif;font-weight:400;font-size:36px;color:var(--orange);letter-spacing:1px;margin-bottom:12px}
.svc-text p{font-size:13px;line-height:15px;margin-bottom:22px}
.svc-text ul{list-style:none}
.svc-text li{font-size:13px;line-height:24px;display:flex;align-items:center;gap:8px}
.svc-text li svg{flex:none}
.svc-text .btn-solid{margin-top:20px;width:120px}
.bedding{left:632px;top:1502px}
.feeding{left:157px;top:1987px}

/* testimonials */
.testi-title{left:0;top:2705px;width:1200px;justify-content:center}
.testi{top:2806px;display:flex;gap:36px}
.avatar{position:relative;width:113px;height:113px;border-radius:50%;background:linear-gradient(160deg,#cfe7e6 0%,#9ccbc9 100%);flex:none}
.avatar .q{position:absolute;right:-4px;bottom:-4px;width:38px;height:38px;border-radius:50%;background:var(--orange);border:3px solid var(--white);color:var(--white);font-family:"Bebas Neue",sans-serif;font-size:34px;line-height:44px;text-align:center}
.testi-body{width:280px;padding-top:6px}
.testi-body .lead{font-size:13px;color:#666;margin-bottom:8px}
.testi-body .quote{font-size:10.5px;line-height:13px;color:#777;margin-bottom:10px}
.testi-body .name{font-family:"Bebas Neue",sans-serif;font-size:18px;color:var(--ink);letter-spacing:.5px}
.stars{display:flex;gap:2px;margin-top:4px}

/* newsletter */
.news-bg{left:0;top:2940px;width:1200px;height:390px;background:var(--brown)}
.news-title{left:168px;top:3100px}
.field{top:3170px;height:48px;background:var(--white);font-size:11px;color:#444;display:flex;align-items:center;padding-left:30px}
.btn-sub{left:903px;top:3170px;width:127px;height:48px;background:var(--orange);color:var(--white);font-family:"Bebas Neue",sans-serif;font-size:18px;display:flex;align-items:center;justify-content:center}

/* blog */
.blog-bg{left:0;top:3300px;width:1200px;height:760px;background:var(--grey)}
.blog-title{left:0;top:3388px;width:1200px;justify-content:center}
.tag{position:absolute;left:18px;top:18px;background:var(--orange);color:var(--white);font-family:"Bebas Neue",sans-serif;font-size:14px;padding:2px 6px;letter-spacing:.5px}
.blog-main-img{left:126px;top:3492px;width:634px;height:245px;background:linear-gradient(180deg,#4d8fd6 0%,#9ec4ea 45%,#d8b66a 62%,#c79a45 100%)}
.blog-main{left:162px;top:3770px;width:570px}
.blog-main h3{font-family:"Bebas Neue",sans-serif;font-weight:400;font-size:22px;color:var(--ink);letter-spacing:.6px}
.meta{font-size:12px;color:var(--orange);margin:6px 0 14px}
.blog-main p{font-size:10.5px;line-height:15.5px;color:#666}
.more{font-size:8px;color:#444;margin-top:14px;letter-spacing:.4px}
.card{left:790px;width:280px;height:246px;background:var(--brown)}
.card .img{position:absolute;left:0;top:0;width:280px;height:165px}
.card .cap{position:absolute;left:16px;top:178px;color:var(--white);font-size:15px;line-height:17px;font-weight:500}
.card .cap span{display:block;color:var(--orange);font-size:12px;font-weight:400;margin-top:3px}
.c1{top:3492px}
.c1 .img{background:linear-gradient(180deg,#b78a5a 0%,#e8ded2 50%,#cdb9a2 100%)}
.c2{top:3758px}
.c2 .img{background:linear-gradient(180deg,#4f8ed0 0%,#a9cbea 45%,#d8aa5a 65%,#b98937 100%)}

/* footer */
.footer-bg{left:0;top:4030px;width:1200px;height:330px;background:var(--brown)}
.footer .brand{position:absolute;left:128px;top:4180px;flex-direction:column;gap:12px}
.footer .brand-name{color:var(--white);font-size:42px}
.fcol h5{font-family:"Roboto",sans-serif;font-weight:500;font-size:13px;color:var(--orange);text-decoration:underline;margin-bottom:14px}
.fcol li{list-style:none;color:var(--white);font-size:11px;line-height:18px;display:flex;gap:8px;align-items:flex-start}
.fcol li svg{flex:none;margin-top:4px}
.f-links{left:451px;top:4180px}
.f-contact{left:653px;top:4182px}
.f-news{left:913px;top:4180px}
.f-email{width:136px;height:24px;background:var(--white);border-radius:2px;font-size:8px;color:#888;display:flex;align-items:center;padding-left:10px}
.f-go{width:24px;height:24px;background:var(--orange);border-radius:2px;display:flex;align-items:center;justify-content:center}
.copy{left:0;top:4358px;width:1200px;height:47px;background:var(--orange);color:var(--brown-deep);font-size:11.5px;display:flex;justify-content:space-between;align-items:center;padding:0 126px}
</style>
</head>
<body>

<!-- top bar -->
<div class="abs topbar">
  <span>Call us : +1 555 014 2273</span>
  <span>Follow us :</span>
  <span class="dots"><i></i><i></i><i></i><i></i><i></i></span>
</div>

<!-- hero -->
<section>
  <div class="abs hero" role="img" aria-label="Aerial photo of red barns and horse stables with paddocks, fading into a brown field"></div>
  <svg class="abs hero-curve" width="1200" height="145" viewBox="0 0 1200 145" aria-hidden="true">
    <path d="M0,47 Q600,220 1200,47 L1200,145 L0,145 Z" fill="#fff"/>
  </svg>
  <header class="abs header">
    <div class="brand"><span class="brand-mark"></span><span class="brand-name">Golden Sheaf</span></div>
    <nav class="nav"><a>Home</a><a>About</a><a>Feed</a><a>Bedding</a><a>Contact Us</a></nav>
  </header>
  <div class="abs btn-quote">Request Qoute</div>
  <div class="abs arrow" style="left:60px;transform:rotate(-45deg)"></div>
  <div class="abs arrow" style="left:1124px;transform:rotate(135deg)"></div>
  <h1 class="abs hero-title display">The best bedding &amp; feed for your<br>horse livestock or household pet</h1>
  <div class="abs hero-btns"><span class="btn btn-solid">Contact Us</span><span class="btn btn-line">Request Qoute</span></div>
</section>

<!-- about -->
<section>
  <h2 class="abs sec-title about-title"><span class="ring"></span>About Us</h2>
  <div class="abs about-sub">Welcome to the Golden Sheaf Bedding &amp; Feed</div>
  <div class="abs about-text">
    <p>Looking for the best bedding and feed for your horse, livestock or household pet look no further. We use premium locally sourced straw and hay in all of our products and are committed in providing quality products and service.</p>
    <p>Your animal deserves the very best in health and comfort to keep them healthy, strong and happy. Our products are designed for horses, livestock (goats, cattle and sheep), small caged animals (rabbits, guinea pigs and more).</p>
    <p>Golden Sheaf offers supply and delivery of fresh bedding as well as removal of waste bedding. Let us deliver you a container of fresh straw and haul your waste bedding away. A full service solution that is sustainable and responsible.</p>
  </div>
  <div class="abs about-img" role="img" aria-label="Group of farm animals: a horse, a cow, a goat, a sheep and a rabbit"></div>

  <div class="abs feature" style="left:112px">
    <span class="ico"><svg width="20" height="20" viewBox="0 0 20 20"><path d="M10 2 L17 5 V10 C17 14 14 17 10 18 C6 17 3 14 3 10 V5 Z" fill="none" stroke="#3b1f0e" stroke-width="1.8"/></svg></span>
    <div><h4>Quality Guaranteed</h4><p>Grown for quality - 100% natural with no chemicals or additives</p></div>
  </div>
  <div class="abs divider" style="left:380px"></div>
  <div class="abs feature" style="left:425px">
    <span class="ico"><svg width="20" height="20" viewBox="0 0 20 20"><circle cx="10" cy="10" r="7" fill="none" stroke="#3b1f0e" stroke-width="1.8"/><path d="M10 6 V10 L13 12" stroke="#3b1f0e" stroke-width="1.8" fill="none"/></svg></span>
    <div><h4>Full Service Solution</h4><p>Dedicated in providing a full service solution of bedding supply &amp; waste removal</p></div>
  </div>
  <div class="abs divider" style="left:707px"></div>
  <div class="abs feature" style="left:758px">
    <span class="ico"><svg width="20" height="20" viewBox="0 0 20 20"><path d="M4 11 L8 15 L16 6" fill="none" stroke="#3b1f0e" stroke-width="2"/></svg></span>
    <div><h4>Convenient &amp; Cost Effective</h4><p>Compressed bags, pellets or bulk products saving in shipping costs</p></div>
  </div>
</section>

<!-- services -->
<section>
  <div class="abs services-bg"></div>
  <svg class="abs curve" style="top:1147px" width="1200" height="95" viewBox="0 0 1200 95" aria-hidden="true">
    <path d="M0,0 L1200,0 L1200,1 Q600,184 0,1 Z" fill="#fff"/>
  </svg>
  <h2 class="abs sec-title light services-title"><span class="ring"></span>Our Services</h2>
  <div class="abs svc"></div>
  <div class="ph svc-img1" role="img" aria-label="Mare and newborn foal resting on golden straw bedding"></div>
  <div class="ph svc-img2" role="img" aria-label="Close-up of a horse muzzle eating hay"></div>

  <div class="abs svc-text bedding">
    <h3>Bedding</h3>
    <p>Hay cubes and pellets are made from premium hay offering a variety of animals a feed that is non-GMO and packed with natural nutrients. These pellets and cubes are less bulky to handle, store and ship.As well, they reduce the amount of wasted feed.</p>
    <ul>
      <li><svg width="12" height="12" viewBox="0 0 12 12"><circle cx="6" cy="6" r="6" fill="#f7931e"/><path d="M3 6 L5.2 8 L9 4" stroke="#4a2511" stroke-width="1.6" fill="none"/></svg>100% Natural Chopped Straw</li>
      <li><svg width="12" height="12" viewBox="0 0 12 12"><circle cx="6" cy="6" r="6" fill="#f7931e"/><path d="M3 6 L5.2 8 L9 4" stroke="#4a2511" stroke-width="1.6" fill="none"/></svg>Low Dust</li>
      <li><svg width="12" height="12" viewBox="0 0 12 12"><circle cx="6" cy="6" r="6" fill="#f7931e"/><path d="M3 6 L5.2 8 L9 4" stroke="#4a2511" stroke-width="1.6" fill="none"/></svg>Chemical &amp; Additive Free</li>
      <li><svg width="12" height="12" viewBox="0 0 12 12"><circle cx="6" cy="6" r="6" fill="#f7931e"/><path d="M3 6 L5.2 8 L9 4" stroke="#4a2511" stroke-width="1.6" fill="none"/></svg>Clean &amp; Highly Absorbent</li>
      <li><svg width="12" height="12" viewBox="0 0 12 12"><circle cx="6" cy="6" r="6" fill="#f7931e"/><path d="M3 6 L5.2 8 L9 4" stroke="#4a2511" stroke-width="1.6" fill="none"/></svg>Cheaper than Wood Shavings</li>
      <li><svg width="12" height="12" viewBox="0 0 12 12"><circle cx="6" cy="6" r="6" fill="#f7931e"/><path d="M3 6 L5.2 8 L9 4" stroke="#4a2511" stroke-width="1.6" fill="none"/></svg>Economic – less used &amp; less wasted</li>
      <li><svg width="12" height="12" viewBox="0 0 12 12"><circle cx="6" cy="6" r="6" fill="#f7931e"/><path d="M3 6 L5.2 8 L9 4" stroke="#4a2511" stroke-width="1.6" fill="none"/></svg>Environmentally Friendly – Recyclable &amp; Compostable</li>
    </ul>
    <span class="btn btn-solid">Read More</span>
  </div>

  <div class="abs svc-text feeding">
    <h3>Feeding</h3>
    <p>Hay cubes and pellets are made from premium hay offering a variety of animals a feed that is non-GMO and packed with natural nutrients. These pellets and cubes are less bulky to handle, store and ship.As well, they reduce the amount of wasted feed.</p>
    <ul>
      <li><svg width="12" height="12" viewBox="0 0 12 12"><circle cx="6" cy="6" r="6" fill="#f7931e"/><path d="M3 6 L5.2 8 L9 4" stroke="#4a2511" stroke-width="1.6" fill="none"/></svg>100% Natural</li>
      <li><svg width="12" height="12" viewBox="0 0 12 12"><circle cx="6" cy="6" r="6" fill="#f7931e"/><path d="M3 6 L5.2 8 L9 4" stroke="#4a2511" stroke-width="1.6" fill="none"/></svg>Chemical &amp; Additive Free</li>
      <li><svg width="12" height="12" viewBox="0 0 12 12"><circle cx="6" cy="6" r="6" fill="#f7931e"/><path d="M3 6 L5.2 8 L9 4" stroke="#4a2511" stroke-width="1.6" fill="none"/></svg>Available in Pellets or Cubes</li>
      <li><svg width="12" height="12" viewBox="0 0 12 12"><circle cx="6" cy="6" r="6" fill="#f7931e"/><path d="M3 6 L5.2 8 L9 4" stroke="#4a2511" stroke-width="1.6" fill="none"/></svg>High Protein Content</li>
      <li><svg width="12" height="12" viewBox="0 0 12 12"><circle cx="6" cy="6" r="6" fill="#f7931e"/><path d="M3 6 L5.2 8 L9 4" stroke="#4a2511" stroke-width="1.6" fill="none"/></svg>Eliminate Waste In Feeding</li>
      <li><svg width="12" height="12" viewBox="0 0 12 12"><circle cx="6" cy="6" r="6" fill="#f7931e"/><path d="M3 6 L5.2 8 L9 4" stroke="#4a2511" stroke-width="1.6" fill="none"/></svg>Clean - Eliminates Dust From Feeding Baled Hay</li>
      <li><svg width="12" height="12" viewBox="0 0 12 12"><circle cx="6" cy="6" r="6" fill="#f7931e"/><path d="M3 6 L5.2 8 L9 4" stroke="#4a2511" stroke-width="1.6" fill="none"/></svg>Cost Effective</li>
    </ul>
    <span class="btn btn-solid">Read More</span>
  </div>

  <svg class="abs curve" style="top:2525px" width="1200" height="91" viewBox="0 0 1200 91" aria-hidden="true">
    <path d="M0,1 Q600,180 1200,1 L1200,91 L0,91 Z" fill="#fff"/>
  </svg>
</section>

<!-- testimonials -->
<section>
  <h2 class="abs sec-title testi-title"><span class="ring"></span>Testimonials</h2>
  <div class="abs testi" style="left:130px">
    <div class="avatar" role="img" aria-label="Portrait photo of customer Clara Mendes"><span class="q">&ldquo;</span></div>
    <div class="testi-body">
      <div class="lead">Grandioribus dicas, ipsae res verba rapiunt</div>
      <div class="quote">Rapiunt; Hoc non est positum in nostra actione. Quod occurrentia fingunt, vincunt Aristonem Haec para/</div>
      <div class="name">Clara Mendes</div>
      <div class="stars"><svg width="62" height="11" viewBox="0 0 62 11"><g fill="#f7931e"><path id="st" d="M5.5 0 L7 3.8 L11 4 L8 6.6 L9 10.5 L5.5 8.4 L2 10.5 L3 6.6 L0 4 L4 3.8 Z"/><use href="#st" x="12.5"/><use href="#st" x="25"/><use href="#st" x="37.5"/><use href="#st" x="50"/></g></svg></div>
    </div>
  </div>
  <div class="abs testi" style="left:636px">
    <div class="avatar" role="img" aria-label="Portrait photo of customer Tomas Varga"><span class="q">&ldquo;</span></div>
    <div class="testi-body">
      <div class="lead">Grandioribus dicas, ipsae res verba rapiunt</div>
      <div class="quote">Rapiunt; Hoc non est positum in nostra actione. Quod occurrentia fingunt, vincunt Aristonem Haec para/</div>
      <div class="name">Tomas Varga</div>
      <div class="stars"><svg width="62" height="11" viewBox="0 0 62 11"><g fill="#f7931e"><use href="#st"/><use href="#st" x="12.5"/><use href="#st" x="25"/><use href="#st" x="37.5"/><use href="#st" x="50"/></g></svg></div>
    </div>
  </div>
</section>

<!-- blog background sits under newsletter curve -->
<div class="abs blog-bg"></div>

<!-- newsletter -->
<section>
  <div class="abs news-bg"></div>
  <svg class="abs curve" style="top:2939px" width="1200" height="50" viewBox="0 0 1200 50" aria-hidden="true">
    <path d="M0,0 L1200,0 L1200,1 Q600,80 0,1 Z" fill="#fff"/>
  </svg>
  <h2 class="abs sec-title light news-title"><span class="ring"></span>Subscribe to Newsletter</h2>
  <div class="abs field" style="left:171px;width:292px">Enter Your Name</div>
  <div class="abs field" style="left:478px;width:408px">Enter Your Email</div>
  <div class="abs btn-sub">Subscribe</div>
  <svg class="abs curve" style="top:3238px" width="1200" height="93" viewBox="0 0 1200 93" aria-hidden="true">
    <path d="M0,0 Q600,150 1200,0 L1200,93 L0,93 Z" fill="#e9e9e9"/>
  </svg>
</section>

<!-- blog -->
<section>
  <h2 class="abs sec-title blog-title"><span class="ring"></span>Our Blog &amp; News</h2>
  <div class="ph blog-main-img" role="img" aria-label="Tractor hauling a trailer stacked with straw bales across a field"><span class="tag">Efficiuntur</span></div>
  <article class="abs blog-main">
    <h3>Efficiuntur volupt nostra actione</h3>
    <div class="meta">By Admin | 4 January 2021</div>
    <p>Per porro dolore nostro, partem integre corpora per ea, tation ornatus mel ad. Brute voluptatibus an est, per cu utroque torquatos, ei eum amet hinc. Ne vix ludus timeam definitionem. His hinc dicunt minimum cu, qui te dico laoreet. Sea ea mucius diceret solens, eos ei nostrud appellantur, an autem vocent novum doctus id mel. Id everti commune accusata melsunt explicabo. Nemo enim ipsam voluptatem quia voluptas sit aspernatur aut odit aut fugit, sit aspernatur aut odit aut fugit, sed quia consequuntur magni dolores eos qui ratione voluptatem sequi nesciunt. Neque porro quisquam est, qui dolorem ipsum quia dolor sit amet, consectetur, adipisci velit, sed quia non numquam eius modi tempora incidunt ut labore et dolore magnam aliquam appellantur, an autem vocent.</p>
    <div class="more">READ MORE &rarr;</div>
  </article>
  <article class="abs card c1">
    <div class="img" role="img" aria-label="Young goats looking over a wooden stall fence"></div>
    <span class="tag">Constructio</span>
    <div class="cap">Sum dolor sit amet cu per<br>porro dolore nostro<span>By Admin | 8 January 2021</span></div>
  </article>
  <article class="abs card c2">
    <div class="img" role="img" aria-label="Round hay bales in a harvested field under a blue sky"></div>
    <span class="tag">Admirabilia</span>
    <div class="cap">Est enim effectrix multarum<br>et magnarum voluptatum.<span>By Admin | 2 January 2021</span></div>
  </article>
</section>

<!-- footer -->
<footer class="footer">
  <div class="abs footer-bg"></div>
  <svg class="abs curve" style="top:4029px" width="1200" height="60" viewBox="0 0 1200 60" aria-hidden="true">
    <path d="M0,0 L1200,0 L1200,14 Q600,100 0,14 Z" fill="#e9e9e9"/>
  </svg>
  <div class="brand"><span class="brand-mark"></span><span class="brand-name">Golden Sheaf</span></div>
  <div class="abs fcol f-links">
    <h5>QUICK LINKS</h5>
    <ul>
      <li><svg width="6" height="8" viewBox="0 0 6 8"><path d="M0 0 L6 4 L0 8 Z" fill="#f7931e"/></svg>Home</li>
      <li><svg width="6" height="8" viewBox="0 0 6 8"><path d="M0 0 L6 4 L0 8 Z" fill="#f7931e"/></svg>About</li>
      <li><svg width="6" height="8" viewBox="0 0 6 8"><path d="M0 0 L6 4 L0 8 Z" fill="#f7931e"/></svg>Feed</li>
      <li><svg width="6" height="8" viewBox="0 0 6 8"><path d="M0 0 L6 4 L0 8 Z" fill="#f7931e"/></svg>Bedding</li>
      <li><svg width="6" height="8" viewBox="0 0 6 8"><path d="M0 0 L6 4 L0 8 Z" fill="#f7931e"/></svg>Contact Us</li>
    </ul>
  </div>
  <div class="abs fcol f-contact">
    <h5>CONTACT US</h5>
    <ul>
      <li><svg width="9" height="11" viewBox="0 0 9 11"><path d="M4.5 0 C7 0 9 2 9 4.3 C9 7 4.5 11 4.5 11 C4.5 11 0 7 0 4.3 C0 2 2 0 4.5 0 Z" fill="#f7931e"/><circle cx="4.5" cy="4.3" r="1.6" fill="#4a2511"/></svg>412 Meadowbrook Road<br>Fairbanks, Alaska 99701</li>
      <li><svg width="10" height="10" viewBox="0 0 10 10"><path d="M2 0 L4 2.5 L3 4 C3.8 5.6 4.6 6.3 6 7 L7.5 6 L10 8 L8.5 10 C4 9.5 0.5 6 0 1.5 Z" fill="#f7931e"/></svg>555-017-8842</li>
      <li><svg width="10" height="8" viewBox="0 0 10 8"><rect width="10" height="8" rx="1" fill="#f7931e"/><path d="M0.5 1 L5 4.5 L9.5 1" stroke="#4a2511" fill="none"/></svg>hello@goldensheaf.example</li>
      <li><svg width="10" height="10" viewBox="0 0 10 10"><circle cx="5" cy="5" r="4.3" fill="none" stroke="#f7931e" stroke-width="1.3"/><path d="M0.7 5 H9.3 M5 0.7 C3 3 3 7 5 9.3 M5 0.7 C7 3 7 7 5 9.3" stroke="#f7931e" fill="none" stroke-width=".9"/></svg>goldensheaf.example</li>
    </ul>
  </div>
  <div class="abs fcol f-news">
    <h5>NEWSLETTER</h5>
    <div style="display:flex;gap:2px"><span class="f-email">Email Address</span><span class="f-go"><svg width="8" height="10" viewBox="0 0 8 10"><path d="M0 0 L8 5 L0 10 Z" fill="#4a2511"/></svg></span></div>
    <h5 style="margin-top:14px;margin-bottom:10px">FOLLOW US</h5>
    <div class="dots" style="gap:4px"><i style="background:#fff;width:15px;height:15px"></i><i style="background:#fff;width:15px;height:15px"></i><i style="background:#fff;width:15px;height:15px"></i><i style="background:#fff;width:15px;height:15px"></i><i style="background:#fff;width:15px;height:15px"></i></div>
  </div>
  <div class="abs copy"><span>Copyright © 2021, Northfield Studio, All Right Reserved</span><span>Delivery in Canada &amp; USA</span></div>
</footer>

</body>
</html>
```